Kestrel Motion LLC Sports Therapy and Soft Tissue Injury solutions

We are a company that specializes in Sports Therapy, Physical therapy, muscular rehab, nutrition plans, and personal training. Kestrel Motion travels around the country and world treating athletes and people in the workforce that have Soft Tissue injuries. We are legally partnered with VMR(Vantor Muscle Recovery/vantorrecovery.example) in treating endurance athletes ex. SteelRidge triathalon. We educate our patients on how to sustain a healthy lifestyle.We need a web design that has a Home page summarizing our services, a Physical therapy page, a Personal training and nutrition page. Our ultimate goal is to build relationships with fitness centers, training facilities, and companies that are implementing preventative health measures for their employees. We want to incorporate the VMR logo and Steelridge logo attached in the website but, we want to use our own name (Kestrel Motion LLC) as the main draw. We will provide literature for the website.

Target Market(s)

Grindlane training gyms, Fitness centers, Dance studios, Companies looking for Corporate Wellness programs

Industry/Entity Type

Health And Wellness

Number of Pages Required

4 page

Font styles to use
Sans Serif

Requirements
Must have
• Stock Photos of Athletes training. Examples of Endurance Athletes and Cross training. A mesh of as many sports and training methods as possible. We are a new company and don't have many photos. Easy accessibility to change and add text as the company grows. Vantor Muscle recovery logo incorporated in the back ground of the website. Always visible but does not take over the web page
Nice to have
• Sleek and cool, and masculine design. We want the website to stand out without focusing on one individual. We want to use the website to brand the company (Kestrel Motion LLC) with easy access to social media platforms

```html
<!DOCTYPE html>
<html lang="en">
<head>
<meta charset="utf-8">
<title>Kestrel Motion – Health And Wellness</title>
<link rel="stylesheet" href="https://fonts.googleapis.com/css2?family=Ubuntu:wght@400;500;700&family=Lato:ital,wght@0,400;0,700;1,400;1,700&display=swap">
<style>
:root{
  --green:#6ea636;
  --blue:#1a73b8;
  --ink:#333;
  --muted:#555;
  --grey-band:#e8e8e8;
  --footer:#1b1b1b;
  --bar:#1a73b8;
  --white:#fff;
}
*{box-sizing:border-box;margin:0;padding:0}
html,body{width:706px;height:1200px;overflow:hidden}
body{position:relative;font-family:'Lato',sans-serif;color:var(--ink);background:var(--white)}
.abs{position:absolute}

/* header */
.site-header{left:0;top:0;width:706px;height:66px;background:linear-gradient(#fff,#f1f1f1);border-top:3px solid #555}
.brand{left:58px;top:14px;display:flex;align-items:center;gap:7px}
.brand-mark{width:34px;height:34px;border-radius:50%;background:var(--green)}
.brand-name{font-family:'Ubuntu',sans-serif;font-weight:500;font-size:17px;color:var(--green);line-height:1}
.brand-tag{font-family:'Ubuntu',sans-serif;font-weight:500;font-size:9px;letter-spacing:.9px;color:var(--blue);margin-top:3px}
.phone-pill{left:440px;top:9px;width:118px;height:22px;border-radius:11px;background:#e6e6e6;font-family:'Lato',sans-serif;font-weight:700;font-size:10px;color:#222;display:flex;align-items:center;padding-left:34px}
.phone-pill .dot{position:absolute;left:0;top:0;width:22px;height:22px;border-radius:50%;background:var(--green);display:flex;align-items:center;justify-content:center}
.social{display:flex;gap:5px}
.social span{width:22px;height:22px;border-radius:50%;background:var(--green);display:block}
.social.top{left:574px;top:9px}
.main-nav{top:45px;left:284px;display:flex;gap:30px;font-family:'Ubuntu',sans-serif;font-weight:500;font-size:8px;letter-spacing:.3px;color:#222}
.main-nav .current{color:var(--green);position:relative}
.main-nav .current::after{content:"";position:absolute;left:-3px;right:-3px;top:16px;height:3px;background:var(--green)}

/* hero */
.hero{left:0;top:66px;width:706px;height:282px;background:linear-gradient(100deg,#3b3a36 0%,#6d6a62 35%,#4b5a3c 60%,#3a3a38 100%)}
.hero-caption{left:0;top:308px;width:706px;height:40px;background:rgba(20,20,20,.75);color:#fff;font-family:'Ubuntu',sans-serif;font-weight:500;font-size:18px;text-align:center;line-height:40px}
.slide-arrow{width:26px;height:26px;background:#333;border:1px solid #777;display:flex;align-items:center;justify-content:center}

/* section titles */
.section-title{left:0;width:706px;text-align:center;font-family:'Ubuntu',sans-serif;font-weight:500;font-size:19px;color:var(--green)}
.section-title em{font-style:normal;color:var(--blue)}
.section-title small{font-size:13px;color:var(--blue)}
.rule{left:330px;width:46px;height:1px;background:#555}

.about-copy{left:68px;top:421px;width:570px;font-size:7.6px;line-height:12px;text-align:center;color:#444}
.about-copy p{margin-bottom:6px}

/* specialties */
.specialties{left:0;top:506px;width:706px;height:246px;background:var(--grey-band)}
.service-card{top:584px;width:186px;height:126px}
.service-card .photo{width:100%;height:100%}
.service-card .label{position:absolute;left:0;bottom:0;width:100%;height:30px;background:rgba(40,40,40,.8);color:#fff;font-family:'Ubuntu',sans-serif;font-weight:500;font-size:12px;line-height:30px;padding-left:44px}
.service-card .label::before{content:"";position:absolute;left:0;top:0;width:33px;height:30px;background:var(--green)}
.mini-arrow{width:16px;height:16px;background:#555;display:flex;align-items:center;justify-content:center}

/* testimonials */
.quote{left:86px;top:838px;width:534px;font-style:italic;font-size:7.6px;line-height:14.5px;text-align:center;color:#444}
.quote b{font-family:'Ubuntu',sans-serif;font-style:normal;font-size:13px;color:#222}
.quote-author{left:0;top:890px;width:706px;text-align:center;font-style:italic;font-weight:700;font-size:9.5px;color:#333}
.avatar{width:52px;height:52px;border-radius:50%;border:3px solid #999;background:radial-gradient(circle at 50% 40%,#b9a897,#555)}
.avatar.active{border-color:var(--green)}

/* footer */
.site-footer{left:0;top:1005px;width:706px;height:168px;background:var(--footer);color:#fff}
.f-head{font-family:'Lato',sans-serif;font-weight:700;font-size:10px;color:#fff}
.f-head::after{content:"";display:block;width:17px;height:2px;background:var(--green);margin-top:9px}
.f-links{list-style:none;font-size:8px;line-height:21.5px}
.f-links li::before{content:"›";color:var(--green);margin-right:6px}
.f-links .strong{font-weight:700}
.field{left:209px;width:126px;height:18px;border:1px solid #ccc;border-radius:2px;font-size:7px;font-weight:700;color:#ddd;padding:4px 7px}
.submit{left:209px;top:1129px;width:126px;height:19px;background:var(--green);color:#fff;font-weight:700;font-size:9px;text-align:center;line-height:19px;border-radius:2px}
.contact-row{left:370px;display:flex;gap:7px;font-size:7.5px;line-height:9.5px}
.badge{background:#777}
.bottom-bar{left:0;top:1173px;width:706px;height:27px;background:var(--bar);color:#fff;font-size:8px;line-height:27px;padding-left:59px}
.social.bottom{left:587px;top:1178px}
.social.bottom span{width:17px;height:17px}
</style>
</head>
<body>

<header class="abs site-header">
  <div class="abs brand">
    <span class="brand-mark"></span>
    <div>
      <div class="brand-name">Kestrel Motion</div>
      <div class="brand-tag">Health And Wellness</div>
    </div>
  </div>
  <div class="abs phone-pill">
    <span class="dot"><svg width="10" height="10" viewBox="0 0 24 24"><path fill="#fff" d="M6.6 10.8a15 15 0 0 0 6.6 6.6l2.2-2.2c.3-.3.7-.4 1-.2 1.1.4 2.3.6 3.6.6.6 0 1 .4 1 1V20c0 .6-.4 1-1 1A17 17 0 0 1 3 4c0-.6.4-1 1-1h3.5c.6 0 1 .4 1 1 0 1.3.2 2.5.6 3.6.1.3 0 .7-.2 1z"/></svg></span>
    (555) 014 - 2290
  </div>
  <div class="abs social top" aria-label="Social media links"><span></span><span></span><span></span></div>
  <nav class="abs main-nav">
    <span class="current">HOME</span>
    <span>PHYSICAL THERAPY</span>
    <span>PERSONAL TRAINING &amp; NUTRITIO</span>
    <span>CONTACT US</span>
  </nav>
</header>

<section>
  <div class="abs hero" role="img" aria-label="Athletes training with kettlebells in a gym while a coach watches"></div>
  <div class="abs slide-arrow" style="left:5px;top:170px"><svg width="10" height="10" viewBox="0 0 10 10"><path d="M7 1 3 5l4 4" stroke="#fff" stroke-width="2" fill="none"/></svg></div>
  <div class="abs slide-arrow" style="left:675px;top:170px"><svg width="10" height="10" viewBox="0 0 10 10"><path d="M3 1l4 4-4 4" stroke="#fff" stroke-width="2" fill="none"/></svg></div>
  <div class="abs hero-caption">We Educate Our Patients On How To Sustain a Healthy Lifestyle !</div>
</section>

<section>
  <h2 class="abs section-title" style="top:369px">About Kestrel Motion <small>Health And Wellness</small></h2>
  <div class="abs rule" style="top:401px"></div>
  <div class="abs about-copy">
    <p>We are a company that specializes in Sports Therapy, Physical therapy, muscular rehab, nutrition plans, and personal training. Kestrel Motion travels around the country and world treating athletes and people in the workforce that have Soft tissue injuries. We educate our patients on how to sustain a healthy lifestyle!</p>
    <p>We build relationships with companies committed to the sustainable health of their employees and patrons. We offer Corporate Health Solutions through VMR®. Contact us today for more information About VMR®.</p>
  </div>
</section>

<section class="abs specialties"></section>
<h2 class="abs section-title" style="top:526px">We <em>Specializes In</em></h2>
<div class="abs rule" style="top:558px"></div>
<div class="abs mini-arrow" style="left:23px;top:638px"><svg width="9" height="6" viewBox="0 0 9 6"><path d="M9 3H1M3 1 1 3l2 2" stroke="#fff" fill="none"/></svg></div>
<div class="abs mini-arrow" style="left:665px;top:638px"><svg width="9" height="6" viewBox="0 0 9 6"><path d="M0 3h8M6 1l2 2-2 2" stroke="#fff" fill="none"/></svg></div>
<div class="abs service-card" style="left:58px">
  <div class="photo" role="img" aria-label="Therapist stretching an athlete's leg with a resistance band" style="background:linear-gradient(120deg,#9a9590,#d8d5d0 60%,#8c8882)"></div>
  <div class="label">Sports Therapy</div>
</div>
<div class="abs service-card" style="left:260px">
  <div class="photo" role="img" aria-label="Physical therapist assessing a patient's knee" style="background:linear-gradient(120deg,#e8ecef,#c9ced2 50%,#8d8e8c)"></div>
  <div class="label">Physical Therapy</div>
</div>
<div class="abs service-card" style="left:462px">
  <div class="photo" role="img" aria-label="Patient doing cable rehab exercise with a therapist" style="background:linear-gradient(120deg,#dfe7ec,#b7c1c8 50%,#d9c3a8)"></div>
  <div class="label">Muscular Rehab</div>
</div>

<section>
  <h2 class="abs section-title" style="top:784px">Client <em>Testimonials</em></h2>
  <div class="abs rule" style="top:816px"></div>
  <p class="abs quote"><b>“</b> Lorem ipsum dolor sit amet, consectetur adipiscing elit, sed do eiusmod tempor incididunt ut labore et dolore magna aliqua. Ut enim veniam, quis nostrud exercitation ullamco laboris nisi ut aliquip ex ea commodo consequat. Duis aute irure dolor in reprehenderit in voluptate velit esse cillum dolore eu fugiat nulla pariatur. Excepteur sint occaecat cupidatat non proident, sunt in culpa qui officia . <b>”</b></p>
  <div class="abs quote-author">- Sconsectetur adipiscing</div>
  <svg class="abs" style="left:346px;top:907px" width="10" height="6" viewBox="0 0 10 6"><path d="M0 6 5 0l5 6z" fill="var(--green)"/></svg>
  <div class="abs avatar" role="img" aria-label="Client portrait" style="left:261px;top:913px"></div>
  <div class="abs avatar active" role="img" aria-label="Client portrait" style="left:324px;top:913px"></div>
  <div class="abs avatar" role="img" aria-label="Client portrait" style="left:386px;top:913px"></div>
</section>

<footer class="abs site-footer"></footer>
<div class="abs f-head" style="left:59px;top:1026px">Quick Links</div>
<ul class="abs f-links" style="left:59px;top:1050px;color:#fff">
  <li class="strong">Home</li><li>Physical Therapy</li><li>Personal Training &amp; Nutritio</li><li>Contact Us</li>
</ul>
<div class="abs f-head" style="left:209px;top:1026px">Quick Inquiry</div>
<div class="abs field" style="top:1058px">Name</div>
<div class="abs field" style="top:1082px">Email</div>
<div class="abs field" style="top:1104px">Message</div>
<div class="abs submit">Submit</div>
<div class="abs f-head" style="left:370px;top:1026px">Contact Details</div>
<div class="abs contact-row" style="top:1058px;color:#fff">
  <svg width="8" height="10" viewBox="0 0 8 10"><path d="M4 0a4 4 0 0 0-4 4c0 3 4 6 4 6s4-3 4-6a4 4 0 0 0-4-4zm0 5.5A1.5 1.5 0 1 1 4 2.5a1.5 1.5 0 0 1 0 3z" fill="var(--green)"/></svg>
  <div><b>Kestrel Motion</b><br>1234- Lorem ipsum dolor sitamet,<br>HARLOW CITY - USA -123456</div>
</div>
<div class="abs contact-row" style="top:1094px;color:#fff">
  <svg width="8" height="8" viewBox="0 0 24 24"><path fill="var(--green)" d="M6.6 10.8a15 15 0 0 0 6.6 6.6l2.2-2.2c.3-.3.7-.4 1-.2 1.1.4 2.3.6 3.6.6.6 0 1 .4 1 1V20c0 .6-.4 1-1 1A17 17 0 0 1 3 4c0-.6.4-1 1-1h3.5c.6 0 1 .4 1 1 0 1.3.2 2.5.6 3.6.1.3 0 .7-.2 1z"/></svg>
  <span>(555) 014 - 2290</span>
</div>
<div class="abs contact-row" style="top:1111px;color:#fff">
  <svg width="8" height="8" viewBox="0 0 8 8"><rect x="1" y="0" width="6" height="3" fill="var(--green)"/><rect x="0" y="3" width="8" height="4" fill="var(--green)"/></svg>
  <span>(555) 014 - 2290</span>
</div>
<div class="abs contact-row" style="top:1129px;color:#fff">
  <svg width="9" height="7" viewBox="0 0 9 7"><rect width="9" height="7" fill="var(--green)"/><path d="M0 0l4.5 4L9 0" stroke="#1b1b1b" fill="none"/></svg>
  <span>hello@kestrelmotion.example</span>
</div>
<div class="abs f-head" style="left:534px;top:1026px">Our Membership</div>
<div class="abs badge" role="img" aria-label="VMR partner badge" style="left:534px;top:1070px;width:104px;height:26px;border-radius:13px"></div>
<div class="abs badge" role="img" aria-label="Steelridge partner badge" style="left:534px;top:1107px;width:114px;height:30px"></div>

<div class="abs bottom-bar">Copyright © 2016 Kestrel Motion. All Rights Reserved.</div>
<div class="abs social bottom" aria-label="Social media links"><span></span><span></span><span></span></div>

</body>
</html>
```